KBT Business Cards

We require business cards for our business. We would like a matte black back to the card, with our logo centred in the middle. The front side of the card is open to design.

Target Market(s)

Clients looking for legal services (professional)

Industry/Entity Type

Legal

Contact Information for Business Card

Doran Kelbrath
Partner
Mobile: 0461 738 524
Email: doran@kbtlaw.co
Website: www.kbtlaw.co
Level 3, 118 Wendmore Street
Sydney NSW 2000

Font styles to use
Other font styles liked:
• Avenir

Colors
f04a50
ffffff
1b1b1b

Requirements
Must have
• Black back with logo included in the centre of the card.
• Our font is Avenir.

```html
<!DOCTYPE html>
<html lang="en">
<head>
<meta charset="utf-8">
<title>KBT Legal – Business Cards</title>
<link href="https://fonts.googleapis.com/css2?family=Nunito+Sans:wght@400;600;800&display=swap" rel="stylesheet">
<style>
  :root {
    --red: #f04a50;
    --red-deep: #c8203f;
    --white: #ffffff;
    --ink: #1b1b1b;
    --black: #111111;
    --stage: #2a2a2a;
    --muted: #d9d9d9;
  }
  * { box-sizing: border-box; margin: 0; padding: 0; }
  html, body { width: 1200px; height: 960px; overflow: hidden; }
  body {
    background: var(--stage);
    font-family: "Nunito Sans", "Avenir", sans-serif;
    display: flex;
    flex-direction: column;
    align-items: center;
    justify-content: center;
    gap: 30px;
  }
  .card {
    position: relative;
    width: 770px;
    height: 440px;
    overflow: hidden;
  }

  /* Back of card */
  .card-back {
    background: radial-gradient(ellipse at center, #262626 0%, var(--ink) 70%);
  }
  .card-back .brand {
    position: absolute;
    left: 50%; top: 46%;
    transform: translate(-50%, -50%);
    display: flex;
    align-items: center;
    gap: 22px;
  }
  .brand-mark {
    width: 46px; height: 46px;
    background: var(--red);
  }
  .brand-name {
    font-weight: 800;
    font-size: 52px;
    letter-spacing: 1px;
    line-height: 1;
  }
  .card-back .brand-name { color: var(--white); }
  .card-back .web {
    position: absolute;
    left: 0; right: 0; bottom: 56px;
    text-align: center;
    color: var(--white);
    font-size: 17px;
    letter-spacing: 6px;
  }
  .card-back .web .domain { color: var(--red); font-weight: 600; }

  /* Front of card */
  .card-front { background: var(--white); }
  .card-front .wave { position: absolute; inset: 0; }
  .card-front .brand {
    position: absolute;
    left: 70px; top: 80px;
    display: flex;
    align-items: center;
    gap: 18px;
  }
  .card-front .brand-mark { width: 34px; height: 34px; }
  .card-front .brand-name { color: var(--ink); font-size: 40px; }

  .person {
    position: absolute;
    right: 44px; top: 62px;
    text-align: right;
    color: var(--white);
  }
  .person-name {
    font-weight: 800;
    font-size: 23px;
    letter-spacing: 1.5px;
    text-transform: uppercase;
  }
  .person-role {
    font-size: 15px;
    letter-spacing: 1.5px;
    text-transform: uppercase;
    color: var(--muted);
    margin-top: 4px;
  }
  .contact {
    position: absolute;
    right: 44px; bottom: 48px;
    list-style: none;
    text-align: right;
    color: var(--white);
    font-size: 17px;
    line-height: 1.55;
  }
  .contact li { display: flex; justify-content: flex-end; align-items: center; gap: 10px; }
  .contact svg { width: 16px; height: 16px; flex: none; }
  .contact .address { display: block; padding-right: 26px; margin-top: 4px; }
</style>
</head>
<body>

  <section class="card card-back" aria-label="Card back">
    <div class="brand">
      <span class="brand-mark"></span>
      <span class="brand-name">KBT LEGAL</span>
    </div>
    <p class="web">www.<span class="domain">kbtlaw</span>.co</p>
  </section>

  <section class="card card-front" aria-label="Card front">
    <svg class="wave" viewBox="0 0 770 440" preserveAspectRatio="none" aria-hidden="true">
      <defs>
        <linearGradient id="ribbon" x1="0" y1="0" x2="0" y2="1">
          <stop offset="0" stop-color="var(--red-deep)"/>
          <stop offset="0.6" stop-color="var(--red)"/>
          <stop offset="1" stop-color="var(--red-deep)"/>
        </linearGradient>
      </defs>
      <path d="M395 0 C480 70 430 210 290 285 C200 335 150 400 140 440 L770 440 L770 0 Z" fill="url(#ribbon)"/>
      <path d="M440 0 C520 80 470 230 330 305 C245 350 205 405 200 440 L770 440 L770 0 Z" fill="var(--black)"/>
    </svg>

    <div class="brand">
      <span class="brand-mark"></span>
      <span class="brand-name">KBT LEGAL</span>
    </div>

    <div class="person">
      <p class="person-name">Doran Kelbrath</p>
      <p class="person-role">Partner</p>
    </div>

    <ul class="contact">
      <li>0461 738 524
        <svg viewBox="0 0 16 16"><rect x="4" y="1" width="8" height="14" rx="1.5" fill="none" stroke="#fff" stroke-width="1.4"/><circle cx="8" cy="12.3" r="0.9" fill="#fff"/></svg>
      </li>
      <li>doran@kbtlaw.co
        <svg viewBox="0 0 16 16"><rect x="1" y="3.5" width="14" height="9" fill="none" stroke="#fff" stroke-width="1.4"/><path d="M1 3.5 L8 9 L15 3.5" fill="none" stroke="#fff" stroke-width="1.4"/></svg>
      </li>
      <li>www.kbtlaw.co
        <svg viewBox="0 0 16 16"><circle cx="8" cy="8" r="6.5" fill="none" stroke="#fff" stroke-width="1.3"/><ellipse cx="8" cy="8" rx="2.8" ry="6.5" fill="none" stroke="#fff" stroke-width="1.1"/><path d="M1.5 8 H14.5" stroke="#fff" stroke-width="1.1"/></svg>
      </li>
      <li class="address">Level 3, 118 Wendmore Street<br>Sydney NSW 2000</li>
    </ul>
  </section>

</body>
</html>
```